Business card design for Automotive workshop

We need a business card for a new automotive repair and tyre shop called Keelstone Prime Automotive located in New Zealand. We are a clean, modern and fresh workshop and company.

Front needs to feature logo,
my name:
Marlo Fenwicke (director)

Address:
48 Tarn Lane
Harrowby 3598

Phone: 07 594 2713
Mobile: 027 451 9362
Email: office@keelstoneautomotive.example.nz
Website: keelstoneautomotive.example.nz

Back needs to feature an area to write down appointment details, date and time.

Also feature a list of jobs and work we do such as,
Vehicle Servicing
All Mechanical Repairs
Warrant of Fitness
Tyres & Wheel Alignments
Automotive Diagnostics
Automotive Parts & Supplies

```html
<!DOCTYPE html>
<html lang="en">
<head>
<meta charset="utf-8">
<title>Keelstone Prime Automotive – Business Card</title>
<link rel="stylesheet" href="https://fonts.googleapis.com/css2?family=Lato:wght@400;700;900&display=swap">
<style>
  :root {
    --backdrop: #2b2b2b;
    --card-white: #ffffff;
    --card-dark: #231f20;
    --brand-red: #e31b23;
    --ink: #111111;
    --muted-logo: #5a5a5a;
    --paper-line: #ffffff;
  }
  * { box-sizing: border-box; margin: 0; padding: 0; }
  html, body {
    width: 1200px; height: 895px; overflow: hidden;
    background: var(--backdrop);
    font-family: "Lato", sans-serif;
  }
  .canvas {
    width: 1200px; height: 895px;
    display: flex; flex-direction: column; align-items: center;
    justify-content: center; gap: 43px;
  }
  .card {
    position: relative; width: 640px; height: 366px; overflow: hidden;
    box-shadow: 0 10px 28px rgba(0,0,0,.55);
  }

  /* Front */
  .card--front { background: var(--card-white); color: var(--ink); }
  .front-brand {
    position: absolute; top: 70px; left: 0; right: 0; text-align: center;
    font-weight: 900; font-size: 31px; letter-spacing: 1px;
    color: var(--brand-red); text-transform: uppercase;
  }
  .front-person {
    position: absolute; top: 176px; left: 40px; width: 225px; text-align: right;
  }
  .person-name {
    font-weight: 900; font-size: 23px; color: var(--brand-red);
    text-transform: uppercase; letter-spacing: .3px;
  }
  .person-role { font-size: 14px; margin-top: 2px; }
  .front-divider {
    position: absolute; top: 150px; left: 286px; width: 1px; height: 104px;
    background: #555;
  }
  .contact-list {
    position: absolute; top: 146px; left: 306px; list-style: none;
    font-size: 13.5px; line-height: 26px;
  }
  .contact-list li { display: flex; align-items: center; gap: 10px; }
  .contact-list svg { width: 14px; height: 14px; flex: none; fill: var(--brand-red); }
  .address-band {
    position: absolute; left: 0; right: 0; bottom: 34px; height: 34px;
    background: var(--ink); color: var(--paper-line);
    display: flex; align-items: center; justify-content: center;
    font-size: 14px; letter-spacing: .3px;
  }

  /* Back */
  .card--back { background: var(--card-dark); color: var(--paper-line); }
  .appointment {
    position: absolute; top: 34px; left: 40px; right: 40px;
    display: flex; align-items: flex-end; gap: 8px; font-size: 13px;
  }
  .appointment-line { display: flex; align-items: flex-end; gap: 8px; }
  .write-box { background: var(--paper-line); height: 26px; }
  .write-box--date { width: 250px; }
  .write-box--time { width: 170px; }
  .appointment-line--time { margin-left: 8px; }
  .back-brand {
    position: absolute; top: 110px; left: 0; right: 0; text-align: center;
    font-weight: 900; font-size: 34px; letter-spacing: 1px;
    color: var(--muted-logo); text-transform: uppercase;
  }
  .services {
    position: absolute; top: 190px; left: 70px; right: 40px;
    display: grid; grid-template-columns: 1fr 1fr; column-gap: 30px;
  }
  .service-list { list-style: none; font-size: 14.5px; line-height: 24px; }
  .service-list li { display: flex; align-items: center; gap: 10px; }
  .service-list li::before {
    content: ""; width: 8px; height: 8px; border: 2px solid var(--brand-red);
    border-radius: 50%; flex: none;
  }
  .web-band {
    position: absolute; left: 0; right: 0; bottom: 0; height: 46px;
    background: var(--brand-red); color: var(--paper-line);
    display: flex; align-items: center; justify-content: center;
    font-weight: 700; font-size: 15px; letter-spacing: .3px;
  }
</style>
</head>
<body>
<main class="canvas">

  <section class="card card--front" aria-label="Card front">
    <div class="front-brand">Keelstone Prime Automotive</div>

    <div class="front-person">
      <p class="person-name">Marlo Fenwicke</p>
      <p class="person-role">Director</p>
    </div>

    <div class="front-divider"></div>

    <ul class="contact-list">
      <li>
        <svg viewBox="0 0 24 24" aria-hidden="true"><path d="M6.6 10.8a15.1 15.1 0 0 0 6.6 6.6l2.2-2.2a1 1 0 0 1 1-.25 11.4 11.4 0 0 0 3.6.57 1 1 0 0 1 1 1V20a1 1 0 0 1-1 1A17 17 0 0 1 3 4a1 1 0 0 1 1-1h3.5a1 1 0 0 1 1 1c0 1.25.2 2.45.57 3.57a1 1 0 0 1-.25 1z"/></svg>
        07 594 2713
      </li>
      <li>
        <svg viewBox="0 0 24 24" aria-hidden="true"><path d="M7 1h10a2 2 0 0 1 2 2v18a2 2 0 0 1-2 2H7a2 2 0 0 1-2-2V3a2 2 0 0 1 2-2zm0 3v14h10V4zm5 15.5a1.2 1.2 0 1 0 0 2.4 1.2 1.2 0 0 0 0-2.4z"/></svg>
        027 451 9362
      </li>
      <li>
        <svg viewBox="0 0 24 24" aria-hidden="true"><path d="M2 5h20v14H2zm2 2v.5l8 5 8-5V7l-8 5z"/></svg>
        office@keelstoneautomotive.example.nz
      </li>
      <li>
        <svg viewBox="0 0 24 24" aria-hidden="true"><path d="M12 2a10 10 0 1 0 0 20 10 10 0 0 0 0-20zm6.9 6h-2.9a15.6 15.6 0 0 0-1.4-3.6A8 8 0 0 1 18.9 8zM12 4a14 14 0 0 1 1.9 4h-3.8A14 14 0 0 1 12 4zM4.3 14a8 8 0 0 1 0-4h3.4a16.5 16.5 0 0 0 0 4zm.8 2h2.9a15.6 15.6 0 0 0 1.4 3.6A8 8 0 0 1 5.1 16zM8 8H5.1a8 8 0 0 1 4.3-3.6A15.6 15.6 0 0 0 8 8zm4 12a14 14 0 0 1-1.9-4h3.8A14 14 0 0 1 12 20zm2.3-6H9.7a14.7 14.7 0 0 1 0-4h4.6a14.7 14.7 0 0 1 0 4zm.3 5.6a15.6 15.6 0 0 0 1.4-3.6h2.9a8 8 0 0 1-4.3 3.6zM16.3 14a16.5 16.5 0 0 0 0-4h3.4a8 8 0 0 1 0 4z"/></svg>
        keelstoneautomotive.example.nz
      </li>
    </ul>

    <div class="address-band">48 Tarn Lane, Harrowby 3598</div>
  </section>

  <section class="card card--back" aria-label="Card back">
    <div class="appointment">
      <div class="appointment-line">
        <span>Date:</span><span class="write-box write-box--date"></span>
      </div>
      <div class="appointment-line appointment-line--time">
        <span>Time:</span><span class="write-box write-box--time"></span>
      </div>
    </div>

    <div class="back-brand">Keelstone Prime Automotive</div>

    <div class="services">
      <ul class="service-list">
        <li>Vehicle Servicing</li>
        <li>All Mechanical Repairs</li>
        <li>Warrant of Fitness</li>
      </ul>
      <ul class="service-list">
        <li>Tyres &amp; Wheel Alignments</li>
        <li>Automotive Diagnostics</li>
        <li>Automotive Parts &amp; Supplies</li>
      </ul>
    </div>

    <div class="web-band">www.keelstoneautomotive.example.nz</div>
  </section>

</main>
</body>
</html>
```